BrindleStaffing Business Card Design

We are a staffing company finding positions for dedicated nurses and physicians.

Target Market(s)

Business Professionals

Industry/Entity Type

Staffing

Contact Information for Business Card

Gordon Pratley
Chairman
417 39th Avenue South
SAINT PETERSBURG FL 33712
813-555-4172 Mobile
813-555-8036 Fax
gpratley@brindlestaffing.com
www.brindlestaffing.com

Font styles to use
Sans Serif

Colors
fbee3e
f04a50
f37122

Requirements
Must have
• Logo Attached, see colors below. We'd like to see Yellow, Orange and Red.

```html
<!DOCTYPE html>
<html lang="en">
<head>
<meta charset="utf-8">
<title>BrindleStaffing Business Card</title>
<link href="https://fonts.googleapis.com/css2?family=Poppins:wght@600&family=Roboto:wght@400;500;700&display=swap" rel="stylesheet">
<style>
  :root {
    --orange: #f37122;
    --red: #f04a50;
    --yellow: #fbee3e;
    --ink: #3d3d3d;
    --paper: #ffffff;
    --backdrop: #e4e4e4;
  }
  * { margin: 0; padding: 0; box-sizing: border-box; }
  html, body { width: 1125px; height: 1200px; overflow: hidden; }
  body { background: var(--backdrop); position: relative; font-family: "Roboto", Arial, sans-serif; }

  .card {
    position: absolute; left: 171px; width: 825px; height: 471px;
    border-radius: 22px; overflow: hidden;
  }
  .card-front { top: 106px; background: var(--paper); }
  .card-back { top: 639px; background: var(--orange); }

  .wordmark {
    position: absolute; font-family: "Poppins", Arial, sans-serif; font-weight: 600;
    letter-spacing: -1px; white-space: nowrap;
  }
  .card-front .wordmark { left: 60px; top: 184px; font-size: 40px; color: var(--orange); }

  .divider { position: absolute; left: 431px; top: 126px; width: 2px; height: 183px; background: var(--orange); }

  .person { position: absolute; left: 468px; top: 115px; }
  .person-name { font-weight: 700; font-size: 34px; color: var(--orange); line-height: 1.1; }
  .person-title { font-weight: 500; font-size: 20px; color: var(--red); line-height: 1.2; }

  .contact-list { position: absolute; left: 468px; top: 203px; list-style: none; }
  .contact-list li { display: flex; align-items: center; height: 26px; font-size: 20px; color: var(--ink); }
  .contact-list svg { width: 20px; height: 20px; margin-right: 11px; fill: var(--orange); flex: none; }

  .front-band { position: absolute; left: 0; top: 0; width: 825px; height: 471px; }
  .address {
    position: absolute; left: 0; right: 0; top: 425px; text-align: center;
    color: var(--paper); font-size: 20px;
  }

  .back-pattern { position: absolute; inset: 0; background: linear-gradient(135deg, var(--orange), var(--red)); }
  .card-back .wordmark {
    left: 0; right: 0; top: 194px; text-align: center; font-size: 58px; color: var(--paper);
  }
  .back-url {
    position: absolute; left: 0; right: 0; top: 404px; text-align: center;
    color: var(--paper); font-size: 18px; letter-spacing: 5.5px;
  }
</style>
</head>
<body>

<section class="card card-front">
  <svg class="front-band" viewBox="0 0 825 471" aria-hidden="true">
    <path d="M0 374 Q412 462 825 374 L825 471 L0 471 Z" fill="var(--orange)"/>
    <path d="M30 382 Q412 442 795 382" fill="none" stroke="var(--yellow)" stroke-width="5"/>
  </svg>

  <div class="wordmark">BrindleStaffing</div>
  <div class="divider"></div>

  <div class="person">
    <div class="person-name">Gordon Pratley</div>
    <div class="person-title">Chairman</div>
  </div>

  <ul class="contact-list">
    <li><svg viewBox="0 0 20 20"><path d="M6 1h8a2 2 0 0 1 2 2v14a2 2 0 0 1-2 2H6a2 2 0 0 1-2-2V3a2 2 0 0 1 2-2zm0 3v11h8V4z"/></svg>813-555-4172</li>
    <li><svg viewBox="0 0 20 20"><path d="M5 2h10v5H5zM2 8h16v7h-3v3H5v-3H2zm5 5v3h6v-3z"/></svg>813-555-8036</li>
    <li><svg viewBox="0 0 20 20"><path d="M2 5h16v11H2zm1.5 1.5v.4L10 11l6.5-4.1v-.4z"/></svg>gpratley@brindlestaffing.com</li>
    <li><svg viewBox="0 0 20 20"><circle cx="10" cy="10" r="8.5"/></svg>www.brindlestaffing.com</li>
  </ul>

  <div class="address">417 39th Avenue South, SAINT PETERSBURG FL 33712</div>
</section>

<section class="card card-back">
  <div class="back-pattern" role="img" aria-label="Tiled pattern of overlapping cross shapes in orange and red tones"></div>
  <div class="wordmark">BrindleStaffing</div>
  <div class="back-url">www.brindlestaffing.com</div>
</section>

</body>
</html>
```